Satchel & Sundial needs new business card design

I need a new business card design. I'm looking for out-of-the-box design which represents the freedom of being a location independent entrepreneur.
I offer coaching, retreats and trips.
I would like to see designs with and without the photo.
Colors I use are black (#000000), green (#25A796) and brown (#D7C38C)
Website satchelandsundial.example

Target Market(s)

location independent entrepreneurs, digital nomads, people looking to swap the 9 to 5 for a lifestyle business

Industry/Entity Type

Business

Contact Information for Business Card

Dorota Falkner
Your Lifestyle Business Coach, Retreat & Trip Leader
http://satchelandsundial.example
hello@satchelandsundial.example
Live a life you don't need a holiday from

Font styles to use
Serif
Sans Serif

Requirements
Must have
• One side should contain only the logo. I would also consider having the "Live a life you don't need a holiday from" on that side too (depending on how it looks)
• Please show both sides on the designs.

```html
<!DOCTYPE html>
<html lang="en">
<head>
<meta charset="utf-8">
<title>Satchel &amp; Sundial – Business Card</title>
<link rel="stylesheet" href="https://fonts.googleapis.com/css2?family=Oswald:wght@400;500;600&display=swap">
<style>
  :root {
    --backdrop: #e8e8e8;
    --ink: #111111;
    --teal: #1f9483;
    --sand: #d2c088;
    --sand-dark: #c8b57c;
    --paper: #ffffff;
    --paper-shade: #ececec;
  }
  * { margin: 0; padding: 0; box-sizing: border-box; }
  html, body {
    width: 1200px; height: 576px; overflow: hidden;
    background: var(--backdrop);
    font-family: "Oswald", "Arial Narrow", sans-serif;
  }
  .canvas { position: relative; width: 1200px; height: 576px; }

  .card {
    position: absolute; top: 138px;
    width: 484px; height: 293px;
    border-radius: 8px; overflow: hidden;
    box-shadow: 0 2px 5px rgba(0,0,0,.25);
  }
  .card--back {
    left: 82px;
    background: linear-gradient(180deg, var(--sand), var(--sand-dark));
  }
  .card--front {
    left: 602px;
    background: linear-gradient(180deg, var(--paper) 30%, var(--paper-shade));
  }

  .wordmark {
    position: absolute; color: var(--ink);
    font-weight: 500; text-transform: uppercase; white-space: nowrap;
    letter-spacing: .5px;
  }
  .card--back .wordmark {
    left: 0; right: 0; top: 124px; text-align: center; font-size: 36px; line-height: 1;
  }
  .card--front .wordmark {
    right: 40px; top: 48px; font-size: 24px; line-height: 1;
  }

  .holder { position: absolute; left: 23px; top: 44px; }
  .holder__name {
    font-size: 19px; font-weight: 600; color: var(--ink); line-height: 1.1;
    text-transform: uppercase;
  }
  .holder__role {
    margin-top: 6px; font-size: 11px; font-weight: 400; color: var(--teal); line-height: 1.35;
  }

  .contact { position: absolute; left: 245px; top: 182px; list-style: none; }
  .contact__item {
    display: flex; align-items: center; gap: 8px;
    font-size: 11.5px; color: var(--ink); height: 20px;
  }
  .contact__item svg { width: 12px; height: 12px; flex: none; }
  .contact__item .accent { color: var(--teal); }

  .social {
    position: absolute; left: 23px; top: 233px;
    display: flex; align-items: center; gap: 8px;
    font-size: 11.5px; color: var(--teal);
  }
  .social__mark { width: 10px; height: 10px; background: var(--ink); border-radius: 2px; }

  .footer-band { position: absolute; left: 0; bottom: 0; width: 484px; height: 40px; }
  .tagline {
    position: absolute; right: 22px; bottom: 12px;
    color: var(--paper); font-size: 13px; font-weight: 400; white-space: nowrap;
  }
</style>
</head>
<body>
<main class="canvas">

  <section class="card card--back" aria-label="Card back">
    <div class="wordmark">Satchel &amp; Sundial</div>
  </section>

  <section class="card card--front" aria-label="Card front">
    <div class="holder">
      <h1 class="holder__name">Dorota Falkner</h1>
      <p class="holder__role">Your Lifestyle Business Coach<br>Retreat &amp; Trip Leader</p>
    </div>

    <div class="wordmark">Satchel &amp; Sundial</div>

    <ul class="contact">
      <li class="contact__item">
        <svg viewBox="0 0 12 12" aria-hidden="true">
          <rect x="0.5" y="2" width="11" height="8" fill="var(--teal)"/>
          <path d="M0.5 2 L6 6.5 L11.5 2" fill="none" stroke="#fff" stroke-width="1"/>
        </svg>
        hello@satchelandsundial.example
      </li>
      <li class="contact__item">
        <svg viewBox="0 0 12 12" aria-hidden="true">
          <circle cx="6" cy="6" r="5.2" fill="none" stroke="var(--teal)" stroke-width="1.2"/>
          <ellipse cx="6" cy="6" rx="2.2" ry="5.2" fill="none" stroke="var(--teal)" stroke-width="1"/>
          <line x1="0.8" y1="6" x2="11.2" y2="6" stroke="var(--teal)" stroke-width="1"/>
        </svg>
        <span>www.<span class="accent">satchelandsundial</span>.example</span>
      </li>
    </ul>

    <div class="social">
      <span class="social__mark" aria-hidden="true"></span>
      <span>/satchelandsundial</span>
    </div>

    <svg class="footer-band" viewBox="0 0 484 40" preserveAspectRatio="none" aria-hidden="true">
      <rect x="0" y="21" width="220" height="19" fill="var(--teal)"/>
      <polygon points="210,3 484,3 484,40 186,40" fill="var(--ink)"/>
    </svg>
    <p class="tagline">Live a life you don’t need a holiday from</p>
  </section>

</main>
</body>
</html>
```